Professional violinist needs business cards

I am trying to attract the following jobs:
-private violin lessons (primarily classical)
-performance gigs (weddings, birthday parties, funerals, etc.)
-collaborations with other artists (studio recordings, performances)

I want to communicate that I have a very high standard of excellence for my work, but I also love people and celebrations.
Values/style words I like are:
love, joy, peace, fun, beauty, authenticity, excellence, warmth, refined/sleek, free spirited. If that's too confusing, just ignore :)

I will attach my favorite business card template that I could find on Canva. The lines are supposed to be like a music staff, which I think is really cool, but I also don't want it to look too busy. I like the simple black and white--I think it looks sharp--but I also am open to other ideas. I also have seen business cards with pictures included that looked great, so I attached an image that could be used as well.

I am also attaching a file that I made of my initials that could be used as a logo, but I'm not sure if it should be included.

Information on the card:
-My name (18 letters total)
-"violinist"
-phone number, email, website

Thank you!

```html
<!DOCTYPE html>
<html lang="en">
<head>
<meta charset="utf-8">
<title>Evelyn Marchetti — Violinist Business Cards</title>
<link rel="stylesheet" href="https://fonts.googleapis.com/css2?family=Dancing+Script:wght@500&family=Cinzel:wght@500&family=Crimson+Text:wght@400;600&display=swap">
<style>
  :root {
    --backdrop: #2b2b2c;
    --card-top: #25282c;
    --card-bottom: #1d2024;
    --staff-line: #474b51;
    --gold: #d9c8a6;
    --ink-light: #eceae6;
    --photo-warm: #6e5f48;
    --photo-shadow: #2e2a24;
  }
  * { margin: 0; padding: 0; box-sizing: border-box; }
  html, body {
    width: 1200px;
    height: 1138px;
    overflow: hidden;
    background: var(--backdrop);
  }
  .canvas {
    position: relative;
    width: 1200px;
    height: 1138px;
  }
  .card {
    position: absolute;
    width: 620px;
    height: 374px;
    border-radius: 14px;
    overflow: hidden;
    background: linear-gradient(160deg, var(--card-top), var(--card-bottom));
    box-shadow: 0 6px 14px rgba(0,0,0,0.35);
  }
  .card--front { left: 275px; top: 186px; }
  .card--back  { left: 276px; top: 608px; }

  .staff {
    position: absolute;
    left: 0;
    top: 92px;
    width: 100%;
    height: 72px;
  }
  .staff__line {
    position: absolute;
    left: 0;
    width: 100%;
    height: 1px;
    background: var(--staff-line);
  }

  .monogram {
    position: absolute;
    left: 0;
    width: 100%;
    text-align: center;
    font-family: "Crimson Text", serif;
    font-weight: 600;
    color: var(--gold);
  }
  .card--front .monogram { top: 100px; font-size: 64px; line-height: 72px; }
  .card--back .monogram  { left: 242px; width: 378px; top: 64px; font-size: 50px; line-height: 60px; }

  .name {
    position: absolute;
    left: 0;
    width: 100%;
    text-align: center;
    font-family: "Dancing Script", cursive;
    font-weight: 500;
    color: var(--ink-light);
  }
  .card--front .name { top: 204px; font-size: 40px; }
  .card--back .name  { left: 242px; width: 378px; top: 136px; font-size: 33px; }

  .role {
    position: absolute;
    left: 0;
    width: 100%;
    text-align: center;
    font-family: "Cinzel", serif;
    font-weight: 500;
    color: var(--ink-light);
    letter-spacing: 3px;
  }
  .card--front .role { top: 255px; font-size: 19px; }
  .card--back .role {
    left: 242px;
    width: 378px;
    top: 180px;
    font-size: 16px;
    display: flex;
    align-items: center;
    justify-content: center;
    gap: 16px;
  }
  .role__rule {
    display: block;
    width: 70px;
    height: 1px;
    background: var(--gold);
  }

  .photo {
    position: absolute;
    left: 0;
    top: 0;
    width: 244px;
    height: 100%;
    background:
      linear-gradient(90deg, rgba(0,0,0,0) 70%, var(--card-top) 100%),
      linear-gradient(180deg, var(--photo-warm), var(--photo-shadow));
  }

  .contact {
    position: absolute;
    left: 242px;
    width: 378px;
    top: 224px;
    list-style: none;
    text-align: center;
    font-family: "Crimson Text", serif;
    font-size: 15.5px;
    line-height: 23.5px;
    color: var(--ink-light);
  }
  .contact__accent { color: var(--gold); }
</style>
</head>
<body>
<div class="canvas">

  <section class="card card--front">
    <div class="staff">
      <span class="staff__line" style="top:0"></span>
      <span class="staff__line" style="top:23px"></span>
      <span class="staff__line" style="top:46px"></span>
      <span class="staff__line" style="top:69px"></span>
    </div>
    <div class="monogram">EM</div>
    <h1 class="name">Evelyn Marchetti</h1>
    <p class="role">VIOLINIST</p>
  </section>

  <section class="card card--back">
    <div class="photo" role="img" aria-label="Portrait of the violinist in a black dress holding a violin and bow beside a stone wall"></div>
    <div class="monogram">EM</div>
    <h2 class="name">Evelyn Marchetti</h2>
    <p class="role"><span class="role__rule"></span>VIOLINIST<span class="role__rule"></span></p>
    <ul class="contact">
      <li>+12 (555) 410-2783</li>
      <li>Evelyn@EvelynMarchetti.com</li>
      <li>www.<span class="contact__accent">EvelynMarchetti</span>.com</li>
      <li>Harrowgate, MD</li>
    </ul>
  </section>

</div>
</body>
</html>
```